A business card design for a dental office. We have Two doctors working here. We practice general de

I already have a logo designed for the office with the name and a slogan.
Now I need to create design for a business card using the same logo.
Details Needed on the front side of the card are :
Bernard K. Oswin, DDS
Gerald M Fenwick, DDS
418 Birch Lane
Millbrook, NH 00000
Phone : 555 019 4831
Fax : 555 019 4832
Website : WWW.BrightmoorToothHaven.Com
Office hours by appointment
On the back side of the card need :
Appointment
Date....................Time...................
With....................................
If unable to keep your appointment, please give 24-48 hours notice in order to avoid broken appointment fee.

Industry/Entity Type

Dental Clinic

Contact Information for Business Card

Bernard K. Oswin, DDS
Gerald M Fenwick, DDS
418 Birch Lane
Millbrook, NH 00000
Phone : 555 019 4831
Fax : 555 019 4832
Appointment

Requirements
Must have
• Keep the Name and slogan on the logo on the front of the card. You can move them around the Logo and Name/Slogan of business (Oswin Family Dentistry/We give you reasons to smile) as you wish to get a feel of the design.
• Bernard K. Oswin, DDS
• Gerald M Fenwick, DDS
• 418 Birch Lane
• Millbrook, NH 00000
• Phone : 555 019 4831
• Fax : 555 019 4832
• WWW.BrightmoorToothHaven.Com
• Keep these three groups above as they are together now in different areas of the front side.
• On the back side of the card need :
• Appointment
• Date....................Time...................
• With....................................
• If unable to keep your appointment, please give 24-48 hours notice in order to avoid broken appointment fee.

```html
<!DOCTYPE html>
<html lang="en">
<head>
<meta charset="utf-8">
<title>Oswin Family Dentistry – Business Card</title>
<link href="https://fonts.googleapis.com/css2?family=Open+Sans:ital,wght@0,400;0,600;0,700;1,400;1,600&display=swap" rel="stylesheet">
<style>
  :root {
    --backdrop: #a3a4a3;
    --card: #f4f4f6;
    --blue: #1f5ea8;
    --band-blue: #1b5ea6;
    --accent-red: #d5303a;
    --text-grey: #555a60;
    --dots: #7a7f86;
    --note-grey: #5c5f64;
    --divider: #c9cbcf;
  }
  * { box-sizing: border-box; margin: 0; padding: 0; }
  html, body { width: 1105px; height: 1200px; overflow: hidden; }
  body {
    background: var(--backdrop);
    font-family: "Open Sans", Arial, sans-serif;
    position: relative;
  }
  .card {
    position: absolute;
    left: 182px;
    width: 746px;
    height: 424px;
    background: var(--card);
    overflow: hidden;
  }
  .card--front { top: 120px; }
  .card--back { top: 637px; height: 427px; }

  /* Front */
  .brand {
    position: absolute;
    left: 0; top: 0;
    width: 359px; height: 379px;
    display: flex; flex-direction: column; align-items: center; justify-content: center;
    gap: 14px;
  }
  .brand__dot {
    width: 26px; height: 26px; border-radius: 50%;
    background: var(--blue);
  }
  .brand__name {
    color: var(--blue);
    font-weight: 600;
    font-size: 19px;
    letter-spacing: 1.2px;
    text-transform: uppercase;
  }
  .divider {
    position: absolute;
    left: 359px; top: 87px;
    width: 1px; height: 193px;
    background: var(--divider);
  }
  .contact {
    position: absolute;
    left: 388px; top: 76px;
    color: var(--text-grey);
  }
  .doctor {
    color: var(--blue);
    font-weight: 600;
    font-size: 26px;
    line-height: 32px;
    white-space: nowrap;
  }
  .doctor__title { font-size: 19px; font-weight: 600; }
  .address {
    margin-top: 14px;
    font-size: 19px;
    line-height: 28px;
  }
  .contact-line {
    display: flex; align-items: center; gap: 10px;
    font-size: 19px; line-height: 29px;
  }
  .contact-line svg { width: 18px; height: 18px; fill: var(--blue); flex: none; }
  .rule-red {
    position: absolute; left: 0; top: 379px;
    width: 100%; height: 3px; background: var(--accent-red);
  }
  .band {
    position: absolute; left: 0; top: 385px;
    width: 100%; height: 39px; background: var(--band-blue);
    color: #fff; font-style: italic; font-weight: 600; font-size: 19px;
    display: flex; align-items: center; justify-content: center;
  }

  /* Back */
  .appt-title {
    position: absolute; left: 39px; top: 32px;
    color: var(--blue); font-weight: 600; font-size: 27px;
  }
  .field {
    position: absolute;
    display: flex; align-items: baseline;
    color: var(--blue); font-size: 20px;
  }
  .field__line {
    flex: 1;
    border-bottom: 2px dotted var(--dots);
    margin-left: 10px;
    transform: translateY(-4px);
  }
  .field__suffix { font-size: 15px; margin-left: 6px; }
  .field--name { left: 39px; top: 100px; width: 648px; }
  .field--date { left: 35px; top: 169px; width: 354px; }
  .field--time { left: 414px; top: 169px; width: 270px; }
  .field--note { left: 39px; top: 231px; width: 641px; }
  .blank-line {
    position: absolute; left: 39px; width: 641px;
    border-bottom: 2px dotted var(--dots);
  }
  .blank-line--1 { top: 292px; }
  .blank-line--2 { top: 331px; }
  .policy {
    position: absolute; left: 0; top: 352px; width: 100%;
    text-align: center;
    color: var(--note-grey); font-style: italic; font-size: 15px; line-height: 22px;
  }
</style>
</head>
<body>

<section class="card card--front">
  <div class="brand">
    <span class="brand__dot"></span>
    <span class="brand__name">Oswin Family Dentistry</span>
  </div>
  <div class="divider"></div>
  <div class="contact">
    <p class="doctor">Bernard K. Oswin, <span class="doctor__title">DDS</span></p>
    <p class="doctor">Gerald M Fenwick, <span class="doctor__title">DDS</span></p>
    <p class="address">418 Birch Lane<br>Millbrook, NH 00000</p>
    <p class="contact-line">
      <svg viewBox="0 0 24 24" aria-hidden="true"><path d="M6.6 10.8a15.1 15.1 0 0 0 6.6 6.6l2.2-2.2c.3-.3.7-.4 1-.2 1.1.4 2.3.6 3.6.6.6 0 1 .4 1 1V20c0 .6-.4 1-1 1A17 17 0 0 1 3 4c0-.6.4-1 1-1h3.5c.6 0 1 .4 1 1 0 1.3.2 2.5.6 3.6.1.3 0 .7-.2 1z"/></svg>
      555 019 4831
    </p>
    <p class="contact-line">
      <svg viewBox="0 0 24 24" aria-hidden="true"><path d="M6 2h9l3 3v4H6z"/><path d="M3 10h18a1 1 0 0 1 1 1v8a1 1 0 0 1-1 1H3a1 1 0 0 1-1-1v-8a1 1 0 0 1 1-1zm2 3v2h4v-2zm0 3v1h4v-1z"/></svg>
      555 019 4832
    </p>
    <p class="contact-line">
      <svg viewBox="0 0 24 24" aria-hidden="true"><path d="M12 2a10 10 0 1 0 0 20 10 10 0 0 0 0-20zm-1 17.9A8 8 0 0 1 4.2 10L9 14.8v1c0 1.1.9 2 2 2zm6.9-2.5A2 2 0 0 0 16 16h-1v-3a1 1 0 0 0-1-1H8v-2h2a1 1 0 0 0 1-1V7h2a2 2 0 0 0 2-2v-.4a8 8 0 0 1 2.9 12.8z"/></svg>
      BrightmoorToothHaven.Com
    </p>
  </div>
  <div class="rule-red"></div>
  <div class="band">Office hours by appointment</div>
</section>

<section class="card card--back">
  <h2 class="appt-title">Next Appointment</h2>
  <div class="field field--name"><span>Name :</span><span class="field__line"></span></div>
  <div class="field field--date"><span>Date :</span><span class="field__line"></span></div>
  <div class="field field--time"><span>Time :</span><span class="field__line"></span><span class="field__suffix">AM/PM</span></div>
  <div class="field field--note"><span>Note :</span><span class="field__line"></span></div>
  <div class="blank-line blank-line--1"></div>
  <div class="blank-line blank-line--2"></div>
  <p class="policy">Please give me 24 hours notice if you are unable to keep your appointment or<br>a cancellation fee may be charged.</p>
</section>

</body>
</html>
```